Statement of Capabilities

We are looking for a fresh new stationary (Word Template) and a new look for our statement of capabilities....logo must be the same.

We are an electrical / lighting contractor-

www.BrightfoldServices.com

Target Market(s)

B2B and government agencies

Industry/Entity Type

Electrical

Colors
eb1f27
0655a3

Requirements
Must have
• LOGO

```html
<!DOCTYPE html>
<html lang="en">
<head>
<meta charset="utf-8">
<title>Brightfold Services – Letterhead</title>
<link href="https://fonts.googleapis.com/css2?family=Questrial&display=swap" rel="stylesheet">
<style>
  :root {
    --brand-red: #eb1f27;
    --brand-blue: #0655a3;
    --brand-navy: #0a3d86;
    --paper: #efefef;
    --backdrop: #d4d4d4;
    --ink-soft: #8a8a8a;
  }
  html, body {
    margin: 0;
    width: 1200px;
    height: 1000px;
    overflow: hidden;
    background: var(--backdrop);
  }
  .letterhead {
    position: absolute;
    left: 258px;
    top: 30px;
    width: 683px;
    height: 940px;
    background: var(--paper);
    box-shadow: 0 2px 10px rgba(0,0,0,0.18);
    font-family: "Questrial", sans-serif;
    overflow: hidden;
  }
  .brand {
    position: absolute;
    left: 56px;
    top: 62px;
    display: flex;
    align-items: center;
    gap: 10px;
  }
  .brand-mark {
    width: 18px;
    height: 18px;
    background: var(--brand-blue);
  }
  .brand-name {
    margin: 0;
    font-size: 27px;
    font-weight: 400;
    color: var(--brand-red);
    line-height: 1;
    letter-spacing: 0.2px;
  }
  .contact {
    position: absolute;
    left: 488px;
    top: 48px;
    font-size: 9px;
    color: var(--ink-soft);
    line-height: 1;
  }
  .contact-list {
    list-style: none;
    margin: 0;
    padding: 0;
  }
  .contact-item {
    display: flex;
    align-items: center;
    gap: 6px;
    height: 12.5px;
  }
  .contact-icon {
    width: 9px;
    height: 9px;
    flex: none;
  }
  .address {
    margin: 8px 0 0;
    font-style: normal;
    line-height: 12.5px;
  }
  .footer-wave {
    position: absolute;
    left: 0;
    bottom: 0;
    width: 683px;
    height: 60px;
    display: block;
  }
</style>
</head>
<body>
  <main class="letterhead">
    <div class="brand">
      <span class="brand-mark"></span>
      <h1 class="brand-name">Brightfold Services</h1>
    </div>

    <div class="contact">
      <ul class="contact-list">
        <li class="contact-item">
          <svg class="contact-icon" viewBox="0 0 10 10" aria-hidden="true"><rect width="10" height="10" rx="1.5" fill="var(--brand-red)"/><path d="M3 2.2l1.1 1.6-.6.7c.4.8 1 1.4 1.8 1.8l.7-.6 1.6 1.1-.5 1c-2.6-.3-4.6-2.3-4.9-4.9z" fill="#fff"/></svg>
          <span>410-555-0186</span>
        </li>
        <li class="contact-item">
          <svg class="contact-icon" viewBox="0 0 10 10" aria-hidden="true"><rect width="10" height="10" rx="1.5" fill="var(--brand-red)"/><rect x="3" y="2" width="4" height="2" fill="#fff"/><rect x="2" y="4.3" width="6" height="2.4" fill="#fff"/><rect x="3" y="7" width="4" height="1.2" fill="#fff"/></svg>
          <span>410-555-0187</span>
        </li>
        <li class="contact-item">
          <svg class="contact-icon" viewBox="0 0 10 10" aria-hidden="true"><rect width="10" height="10" rx="1.5" fill="var(--brand-red)"/><rect x="2" y="3" width="6" height="4" fill="none" stroke="#fff" stroke-width="0.8"/><path d="M2 3l3 2.3L8 3" fill="none" stroke="#fff" stroke-width="0.8"/></svg>
          <span>info@BrightfoldServices.com</span>
        </li>
        <li class="contact-item">
          <svg class="contact-icon" viewBox="0 0 10 10" aria-hidden="true"><rect width="10" height="10" rx="1.5" fill="var(--brand-red)"/><circle cx="5" cy="5" r="2.8" fill="none" stroke="#fff" stroke-width="0.7"/><path d="M2.2 5h5.6M5 2.2c-1.4 1.6-1.4 4 0 5.6M5 2.2c1.4 1.6 1.4 4 0 5.6" fill="none" stroke="#fff" stroke-width="0.6"/></svg>
          <span>www.BrightfoldServices.com</span>
        </li>
      </ul>
      <address class="address">
        214 Harbor Ave Suite B<br>
        Glenfield Maryland 21000
      </address>
    </div>

    <svg class="footer-wave" viewBox="0 0 683 60" preserveAspectRatio="none" aria-hidden="true">
      <path d="M0 30 C 180 28, 330 8, 480 6 C 570 5, 640 18, 683 30 L683 60 L0 60 Z" fill="var(--brand-red)"/>
      <path d="M0 44 C 190 38, 340 18, 490 14 C 580 12, 645 26, 683 38 L683 60 L0 60 Z" fill="#ffffff"/>
      <path d="M60 60 C 220 44, 360 24, 500 20 C 590 18, 650 32, 683 42 L683 60 Z" fill="var(--brand-red)"/>
      <path d="M120 60 C 260 48, 390 30, 510 27 C 595 25, 650 37, 683 46 L683 60 Z" fill="var(--brand-navy)"/>
    </svg>
  </main>
</body>
</html>
```